Zimbal, a future commerce website

Zimbal will be a commerce website; the project is quite large, and for now I just require three pages and the main bar to be crafted; If chosen your design, I will require you to work with me in a freelance job for the rest of the site to be made.
The following is one way to put Zimbal’s building blocks; you can propose another.
A list of webpages, whose design I like, is in the first document.
-Design specification
Zimbal’s interface should be minimal and intuitive.
Its design should make the user perceive Zimbal as innovative; I will incline for an out of the box design.
--Main bar
It will contain the site logo, a search bar, and four buttons, listed below.
---Notifications button
It will display a sidebar with containers; each container will have an icon, the notification, and one or two buttons; two example notifications and its respective buttons are in the second document.
It shall stand out when there are unseen notifications.
---Shopping cart button
A sidebar will be toggled on click with added product previews.
---Sell Button
---Account button
When clicked it will display a pane whose elements will depend on the user
status.
----If logged
It will display seller’s store image, a button linking to the main section of the account section, a button linking to in-process bought items of the account section, and a button linking to in-process sold items of the account section.
----If not logged
It will contain the elements for the user to either log in or register; for the former, email or username and password will be asked, for the latter, username, email, and password, this last one being asked twice.
--Product previews
Each, will have a title, a product image, and the product’s most important characteristics; most characteristics will have alongside an icon, which will display on mouse over the characteristic name, or, a name. Characteristics of two product categories whose product previews will contain an icon alongside are in the third document.
--Main page
Product previews of several categories will be displayed here; in order to reflect recommendation, some should have distinct size.
A list of categories will be present in this page; it may be toggled by a button contained in the main bar, or be displayed permanently.
A text conveying the message that all purchases made with Zimbal payment system are protected will be contained in a full width element which will be positioned below the main bar of this page; a “Learn more” link will be positioned in this element.
--Product page creation page
It will be displayed as part of the publication page.
It will be a "what you see is what you get" design system; the user will choose from several templates and fill the appropriate spaces; where text must be put, sample text will be present, and, where an image must, a plus sign and a “Add image” text will be present; submit please two templates; for the user to be able to add more content, at the bottom of the template there will be four layouts, upon click of one, it will be added.
Regarding the shipping menu, there will always be an empty box with a plus sign and a “Add shipping option” text, if clicked the user will be able to either fill it with company name, shipping time, and price, or to put the text “Arrange with seller” in it (if there is no other box with that text).
--Product page
It will not occupy the whole viewport; there will be vertical holes at the leftmost and rightmost parts of the viewport.
It will contain: price (which should include shipping in type one publications), sale price (for some product pages), countdown of sale price, average seller’s handling time, seller’s reputation indicator as measured by percentage of positive reviews received, seller’s store/profile image, seller’s username, a shipping menu consisting of boxes (selected will be displayed differently), “Buy” and “Add to cart” buttons, a section to view and ask questions, and seller provided images and text.
Previews of similar products will also be present.
Reason: Designs still require some work

```html
<!DOCTYPE html>
<html lang="en">
<head>
<meta charset="utf-8">
<title>Zimbal — Home</title>
<link href="https://fonts.googleapis.com/css2?family=Open+Sans:wght@400;600;700;800&family=Oswald:wght@500;600&display=swap" rel="stylesheet">
<style>
:root{
  --ink:#3a3f45;
  --ink-deep:#2c3035;
  --footer:#3e444b;
  --footer-base:#31363b;
  --text:#4a4f55;
  --muted:#8a9097;
  --line:#d9dcdf;
  --panel:#eef0f2;
  --white:#ffffff;
  --accent:#d8453b;
  --hero-a:#7d95ad;
  --hero-b:#b9c7d2;
}
*{box-sizing:border-box;margin:0;padding:0}
html,body{width:735px;height:1200px;overflow:hidden}
body{font-family:"Open Sans",Arial,sans-serif;color:var(--text);background:var(--white);position:relative}
a{color:inherit;text-decoration:none}

/* utility bar */
.utility-bar{position:absolute;top:0;left:0;width:735px;height:24px;background:var(--ink);display:flex;align-items:center;justify-content:space-between;padding:0 59px}
.social{display:flex;gap:6px}
.social span{width:9px;height:9px;border-radius:50%;background:#aab1b8;display:block}
.utility-links{display:flex;gap:14px;font-size:8px;color:#d4d8dc}

/* main bar */
.main-bar{position:absolute;top:24px;left:0;width:735px;height:44px;display:flex;align-items:center;padding:0 59px;border-bottom:1px solid var(--line)}
.brand{display:flex;align-items:center;gap:6px;font-weight:800;font-size:17px;color:var(--ink);letter-spacing:.5px}
.brand i{width:10px;height:10px;background:var(--accent);display:block}
.search{margin-left:22px;width:130px;height:20px;border:1px solid var(--line);font-size:8px;color:var(--muted);display:flex;align-items:center;padding-left:8px}
.bar-buttons{margin-left:auto;display:flex;gap:5px}
.bar-btn{height:20px;padding:0 9px;background:var(--ink);color:var(--white);font-size:8px;font-weight:600;display:flex;align-items:center;gap:4px}
.bar-btn svg{width:8px;height:8px}

/* hero */
.hero{position:absolute;top:68px;left:0;width:735px;height:276px;background:linear-gradient(180deg,var(--hero-a) 0%,var(--hero-b) 65%,#8b8d7a 100%);color:var(--white);text-align:center}
.hero-copy{position:absolute;top:78px;left:0;width:100%}
.hero .kicker{font-size:20px;font-weight:400;letter-spacing:1px}
.hero h1{font-size:44px;font-weight:800;line-height:1.05;letter-spacing:1px}
.hero .sub{font-size:15px;font-weight:700;letter-spacing:1px;margin-top:2px}
.learn{display:inline-block;margin-top:18px;border:2px solid var(--white);padding:7px 14px;font-size:11px;font-weight:700;letter-spacing:1px}
.dots{position:absolute;bottom:12px;left:0;width:100%;display:flex;justify-content:center;gap:5px}
.dots span{width:5px;height:5px;border-radius:50%;background:rgba(255,255,255,.55)}
.dots span:first-child{background:var(--white)}

/* categories */
.categories{position:absolute;top:382px;left:59px;width:132px;height:510px;background:var(--panel);border:1px solid var(--line);overflow:hidden}
.categories h2{background:var(--ink);color:var(--white);font-family:"Oswald",sans-serif;font-weight:500;font-size:13px;letter-spacing:.5px;padding:10px 9px}
.categories ul{list-style:none;padding:6px 9px}
.categories li{font-size:7px;line-height:15.5px;color:var(--text);white-space:nowrap;overflow:hidden}

/* product sections */
.section-title{position:absolute;left:233px;font-family:"Oswald",sans-serif;font-weight:600;font-size:19px;color:var(--ink);letter-spacing:.5px}
.product-row{position:absolute;left:233px;width:443px;display:flex;justify-content:space-between}
.card{width:101px;border:1px solid var(--line);background:var(--white);padding:6px;text-align:center}
.card-image{height:84px}
.card-name{font-size:6.5px;font-weight:700;color:var(--ink);margin:6px 0 5px;letter-spacing:.3px}
.buy{display:inline-flex;align-items:center;gap:3px;background:var(--ink);color:var(--white);font-size:6.5px;padding:4px 9px}
.buy svg{width:6px;height:6px}

/* promo */
.promo{position:absolute;top:588px;left:233px;width:443px;height:88px;background:#eceded;display:flex}
.promo-image{width:200px;height:100%;background:linear-gradient(90deg,#c9c4bf,#8f8a86 60%,#e2e2e2)}
.promo-copy{flex:1;padding:12px 18px;text-align:right;color:var(--ink)}
.promo-copy .dates{font-size:14px;font-weight:700}
.promo-copy .offer{font-size:28px;font-weight:800;line-height:1.05}
.promo-copy .note{font-size:7px;font-weight:700;color:var(--accent);letter-spacing:.5px}

/* footer */
.footer{position:absolute;top:972px;left:0;width:735px;height:198px;background:var(--footer);color:#c9ced3;display:flex;padding:26px 59px 0;gap:0}
.footer h3{font-family:"Oswald",sans-serif;font-weight:500;font-size:16px;color:var(--white);margin-bottom:10px;letter-spacing:.5px}
.footer p,.footer li{font-size:7px;line-height:11px}
.col-about{width:173px;padding-right:14px}
.col-about p+p{margin-top:9px}
.col-support{width:140px}
.col-support ul{list-style:none}
.col-news{width:158px;padding-right:14px}
.news-input{margin-top:10px;height:20px;width:118px;background:var(--white);color:var(--muted);font-size:7px;display:flex;align-items:center;padding-left:6px}
.news-btn{display:inline-block;margin-top:10px;background:var(--ink-deep);color:var(--white);font-size:7px;padding:4px 8px}
.col-contact p{margin-bottom:2px}
.cards{display:flex;gap:3px;margin-top:6px}
.cards span{width:14px;height:9px;background:#9aa2aa;display:block}
.cards span:nth-child(2){background:#c9a349}
.cards span:nth-child(3){background:#7fa0c2}
.base-bar{position:absolute;top:1170px;left:0;width:735px;height:30px;background:var(--footer-base);display:flex;align-items:center;justify-content:space-between;padding:0 59px;font-size:7px;color:#9aa1a8}
</style>
</head>
<body>

<header class="utility-bar">
  <div class="social"><span></span><span></span><span></span><span></span></div>
  <nav class="utility-links"><a>Home</a><a>Buyers</a><a>Suppliers</a><a>Credit cards</a><a>Support</a></nav>
</header>

<div class="main-bar">
  <div class="brand"><i></i>ZIMBAL</div>
  <div class="search">Enter Your Keyword</div>
  <div class="bar-buttons">
    <a class="bar-btn"><svg viewBox="0 0 10 10"><path d="M5 1a3 3 0 0 0-3 3v3H1v1h8V7H8V4a3 3 0 0 0-3-3zM4 9h2" fill="#fff" stroke="#fff" stroke-width=".6"/></svg>Notifications</a>
    <a class="bar-btn"><svg viewBox="0 0 10 10"><path d="M0 1h2l1.5 5h5L10 3H3" fill="none" stroke="#fff" stroke-width="1"/><circle cx="4" cy="8.5" r="1" fill="#fff"/><circle cx="8" cy="8.5" r="1" fill="#fff"/></svg>Shopping cart</a>
    <a class="bar-btn"><svg viewBox="0 0 10 10"><path d="M1 5l4-4h4v4l-4 4z" fill="#fff"/></svg>Sell</a>
    <a class="bar-btn"><svg viewBox="0 0 10 10"><circle cx="5" cy="3" r="2.2" fill="#fff"/><path d="M1 10a4 4 0 0 1 8 0z" fill="#fff"/></svg>Account</a>
  </div>
</div>

<section class="hero" role="img" aria-label="Photo of a happy shopper with arms wide open under a bright sky">
  <div class="hero-copy">
    <p class="kicker">ALL PURCHASES MADE WITH</p>
    <h1>ZIMBAL PAYMENT</h1>
    <p class="sub">SYSTEM ARE PROTECTED</p>
    <a class="learn">LEARN MORE</a>
  </div>
  <div class="dots"><span></span><span></span><span></span></div>
</section>

<aside class="categories">
  <h2>CATEGORIES</h2>
  <ul>
    <li>Automobiles and Motorcycles</li><li>Baby Supplies and Toys</li><li>Bags and Shoes</li><li>Beauty Care and Cosmetics</li><li>Bike, Bicycle and Accessories</li><li>Computer Products</li><li>Construction Materials</li><li>Consumer Electronics</li><li>Electrical and Electronics</li><li>Fasteners</li><li>Food, Beverages and Tobacco</li><li>Gifts and Crafts</li><li>Hardware</li><li>Home and Garden</li><li>Jewelry and Timepieces</li><li>Lighting</li><li>Machinery</li><li>Medical Appliances</li><li>Metal Alloys</li><li>Mould and Tooling</li><li>Networking and Telecom</li><li>Office Supplies and Stationery</li><li>Packaging and Printing</li><li>Plastics</li><li>Protection and Security</li><li>Rubber</li><li>Services</li><li>Sports and Entertainment</li><li>Textiles and Garments</li></ul>
</aside>

<h2 class="section-title" style="top:380px">HOT PRODUCTS</h2>
<div class="product-row" style="top:412px">
  <div class="card"><div class="card-image" role="img" aria-label="Colourful cosmetic bottles" style="background:linear-gradient(135deg,#f6b7d2,#9fd3ea,#f4e19a)"></div><p class="card-name">COSMETIC PRODUCTS</p><a class="buy"><svg viewBox="0 0 10 10"><path d="M0 1h2l1.5 5h5L10 3H3" fill="none" stroke="#fff" stroke-width="1.2"/></svg>Buy Now</a></div>
  <div class="card"><div class="card-image" role="img" aria-label="Desktop computer monitor" style="background:linear-gradient(180deg,#f2f3f4,#5a6068 45%,#e8e9ea)"></div><p class="card-name">COMPUTER</p><a class="buy"><svg viewBox="0 0 10 10"><path d="M0 1h2l1.5 5h5L10 3H3" fill="none" stroke="#fff" stroke-width="1.2"/></svg>Buy Now</a></div>
  <div class="card"><div class="card-image" role="img" aria-label="Home appliances group" style="background:linear-gradient(135deg,#e5e7e9,#a9aeb3,#dfe1e3)"></div><p class="card-name">ELECTRONICS</p><a class="buy"><svg viewBox="0 0 10 10"><path d="M0 1h2l1.5 5h5L10 3H3" fill="none" stroke="#fff" stroke-width="1.2"/></svg>Buy Now</a></div>
  <div class="card"><div class="card-image" role="img" aria-label="Gold rings" style="background:linear-gradient(135deg,#f7f1df,#d9b45a,#f5efe0)"></div><p class="card-name">JEWELLERY</p><a class="buy"><svg viewBox="0 0 10 10"><path d="M0 1h2l1.5 5h5L10 3H3" fill="none" stroke="#fff" stroke-width="1.2"/></svg>Buy Now</a></div>
</div>

<section class="promo">
  <div class="promo-image" role="img" aria-label="Photo of a shopper holding a payment card"></div>
  <div class="promo-copy">
    <p class="dates">Aug 01 to Aug 15</p>
    <p class="offer">20% OFFERS</p>
    <p class="note">ALL CREDIT CARD</p>
  </div>
</section>

<h2 class="section-title" style="top:700px">NEW PRODUCTS</h2>
<div class="product-row" style="top:732px">
  <div class="card"><div class="card-image" role="img" aria-label="Red leather handbag" style="background:linear-gradient(135deg,#fbeaea,#c8312b,#f6e3e2)"></div><p class="card-name">BAGS</p><a class="buy"><svg viewBox="0 0 10 10"><path d="M0 1h2l1.5 5h5L10 3H3" fill="none" stroke="#fff" stroke-width="1.2"/></svg>Buy Now</a></div>
  <div class="card"><div class="card-image" role="img" aria-label="Pink running shoes" style="background:linear-gradient(135deg,#fdeef4,#e8528b,#fbe9f0)"></div><p class="card-name">FOOTWEAR</p><a class="buy"><svg viewBox="0 0 10 10"><path d="M0 1h2l1.5 5h5L10 3H3" fill="none" stroke="#fff" stroke-width="1.2"/></svg>Buy Now</a></div>
  <div class="card"><div class="card-image" role="img" aria-label="Colourful stacking toys" style="background:linear-gradient(135deg,#f4d35e,#4fa3d9,#e8594f)"></div><p class="card-name">TOYS</p><a class="buy"><svg viewBox="0 0 10 10"><path d="M0 1h2l1.5 5h5L10 3H3" fill="none" stroke="#fff" stroke-width="1.2"/></svg>Buy Now</a></div>
  <div class="card"><div class="card-image" role="img" aria-label="Set of hand tools" style="background:linear-gradient(135deg,#eee,#c2473f 40%,#6e7378)"></div><p class="card-name">SET OF HANDTOOLS</p><a class="buy"><svg viewBox="0 0 10 10"><path d="M0 1h2l1.5 5h5L10 3H3" fill="none" stroke="#fff" stroke-width="1.2"/></svg>Buy Now</a></div>
</div>

<footer class="footer">
  <div class="col-about">
    <h3>ZIMBAL</h3>
    <p>Zimbal brings buyers and sellers together in one calm, secure marketplace built for everyday shopping.</p>
    <p>Every order paid through our payment system is protected from checkout until the parcel reaches your door safely.</p>
  </div>
  <div class="col-support">
    <h3>SUPPORT</h3>
    <ul><li>Account</li><li>Forgot Password</li><li>Support Center</li><li>Contact Us</li><li>Return</li><li>Privacy Policy</li></ul>
  </div>
  <div class="col-news">
    <h3>NEWSLETTER</h3>
    <p>Enter your email address to receive the latest offers and news.</p>
    <div class="news-input">Enter Your Email</div>
    <a class="news-btn">Submit</a>
  </div>
  <div class="col-contact">
    <h3>CONTACT US</h3>
    <p>Questions about an order? Our team answers every day.</p>
    <p>+00 555 0192 480</p>
    <p>hello@zimbal-shop.net</p>
    <div class="cards"><span></span><span></span><span></span></div>
  </div>
</footer>
<div class="base-bar">
  <span>© 2015 Zimbal. All rights reserved.</span>
  <div class="social"><span></span><span></span><span></span><span></span></div>
</div>

</body>
</html>
```